revised: 'kelvale ironworks' logo -or- business card

we require a business card or a logo that can be used on a business card & other stationery

(i've just recently decided to open this contest up to logo designs as well - but if you have already been working on a card concept, please feel free to continue with it & submit!)

-

We design and build custom brackets and fixings for our customers and their castles, i.e. homes, offices, workshops, farms etc. Our products might be used to:
- brace or support structures, such as houses, decks, small bridges, etc.
- connect any building material to another
- or could simply be a unique piece that exists as a talking point

As part of our design process we would produce drawings/plans/blue prints/prototypes of the product. Our designs factor in multiple elements, from the materials being joined, the client's taste, and the overall durability demanded by the application - if necessary, the bracket may also be endorsed by a third party, such as a stuctural or mechanical engineer.

The build process takes part in our workshop and on the client's site - some elements may be manufactured off-site, depending on the design chosen and the materials used.

Our brackets are designed to our customers' tastes and could be made to be hidden within the structure or exposed to create interest. Our brackets can be large or small, or be neat with clean lines or take on more of an industrial look.
Updates

please note brief has been updated with a more specific description of our business activity

i have also added the final drawing that was used to water-jet the bracket shown in the photos

also, you will note i changed the title to 'logo + business card'

i don't expect a logo as a discrete artefact of the job, however, i expect that some or all elements on the face of the business card will lend themselves to the street sign (as stated in the original brief) as well as any future logo used on letter heads, invoices, etcetera

another update - changed the allowable entries to include logo's only, as well as business cards

Industry/Entity Type

Industrial

Requirements
Must have
• the face should have the name 'Kelvale Ironworks' (or no/all-caps)

the number '75' in the logo, which will also be turned into a conservative (residential) street sign ('75' being a street number) - '75' should stand alone -OR- be readily identified by someone who has previously received a business card

i need to make this '75' and any associated 'framing', so it should be transferrable to cad/dxf for machining, laser/water-cutting, brazing/welding, etcet.

(on that note, the winning designer will be able to share their vision for this sign and we'll adhere to it ... within the realms of possibility! if you're happy with the result then you could include it in your portfolio)
Nice to have
• one side of the card needs a majority of space for quotes, hand-written information, etcet. so this side should be white or a light, complimentary colour suitable for black/blue pen

the following should appear somewhere on the card (there is no email or website) :
- name : Dana Morrow (Proprietor)
- mobile phone number : +61 (0) 498 761203
- abn: 58 904 617 235

any combination of the following (or equivalent) text:

* 'your castle' - this is slang for your house/place (i prefer this to 'home' as 1: it can apply to a place of business, and 2: for me at least, it conjurs images of wrought iron, brass, hardwood & stone)

* unique

* ...

```html
<!DOCTYPE html>
<html lang="en">
<head>
<meta charset="utf-8">
<title>Kelvale Ironworks – Business Card</title>
<link rel="stylesheet" href="https://fonts.googleapis.com/css2?family=Roboto+Condensed:wght@300;400;500&display=swap">
<style>
  :root {
    --page-bg: #e4e5e7;
    --card-brown: #352312;
    --amber: #f9a62b;
    --amber-deep: #ef7f1f;
    --note-panel: #e2ddd8;
    --rule: #9a938c;
    --ink-light: #ece5dc;
    --ink-muted: #8c7a66;
  }
  * { margin: 0; padding: 0; box-sizing: border-box; }
  html, body {
    width: 1200px;
    height: 900px;
    overflow: hidden;
    background: var(--page-bg);
    font-family: "Roboto Condensed", "Arial Narrow", sans-serif;
  }
  .canvas { position: relative; width: 1200px; height: 900px; }

  .card {
    position: absolute;
    left: 278px;
    width: 641px;
    height: 356px;
    border-radius: 29px;
    background: var(--card-brown);
    overflow: hidden;
  }
  .card--front { top: 47px; }
  .card--back  { top: 474px; }

  /* Front */
  .wordmark {
    position: absolute;
    left: 150px;
    top: 133px;
    width: 150px;
    font-weight: 500;
    font-size: 30px;
    line-height: 34px;
    letter-spacing: 0.5px;
    text-transform: uppercase;
    color: var(--amber);
    text-align: center;
  }
  .wordmark-square {
    position: absolute;
    left: 380px;
    top: 128px;
    width: 100px;
    height: 100px;
    background: var(--amber);
  }

  /* Back */
  .note-panel {
    position: absolute;
    left: 31px;
    top: 32px;
    width: 355px;
    height: 294px;
    border-radius: 10px;
    background: var(--note-panel);
  }
  .note-line {
    position: absolute;
    left: 19px;
    right: 19px;
    border-top: 1px dashed var(--rule);
  }
  .contact {
    position: absolute;
    left: 400px;
    top: 46px;
    color: var(--ink-light);
  }
  .contact-name { font-weight: 300; font-size: 21px; line-height: 24px; }
  .contact-role { font-weight: 300; font-size: 13px; line-height: 16px; }
  .contact-phones {
    margin-top: 30px;
    font-weight: 300;
    font-size: 21px;
    line-height: 27px;
  }
  .abn {
    position: absolute;
    left: 163px;
    top: 331px;
    font-size: 11px;
    font-weight: 300;
    color: var(--ink-muted);
  }
</style>
</head>
<body>
<main class="canvas">

  <section class="card card--front" aria-label="Card face">
    <div class="wordmark">Kelvale<br>Ironworks</div>
    <div class="wordmark-square" aria-hidden="true"></div>
  </section>

  <section class="card card--back" aria-label="Card reverse">
    <div class="note-panel" aria-label="Space for handwritten notes">
      <div class="note-line" style="top:51px"></div>
      <div class="note-line" style="top:88px"></div>
      <div class="note-line" style="top:126px"></div>
      <div class="note-line" style="top:163px"></div>
      <div class="note-line" style="top:201px"></div>
      <div class="note-line" style="top:238px"></div>
      <div class="note-line" style="top:276px"></div>
    </div>

    <div class="contact">
      <p class="contact-name">Dana Morrow</p>
      <p class="contact-role">Proprietor</p>
      <p class="contact-phones">0498 761203<br>+61 (0) 498 761203</p>
    </div>

    <p class="abn">abn. 58 904 617 235</p>
  </section>

</main>
</body>
</html>
```